Local massage therapist needs some new marketing material

Hi there! I am a massage therapist here in Denver, CO in Alder Bend(shopping and art district) of the city. My business is called Lumo Bodywork of Denver. My practice has an eastern influence and I do reflexology, thai massage and use Chinese herbs, etc. I know all my clients and pay close attention to details. I am also very respectful of tradition and it shows in how I work. I tend to like modern, clean, fun, Asian designs. I am wanting a new business card and brochure. I have a logo and branding for my business that I want used in the design. Currently, the sign for my building is purple and I think my logo was designed to be purple. I will attach pictures of it and can send whatever files are necessary so it can be integrated into the brochure, etc. I like the purple but open to using other colors as well. Thanks!
My website is lumobodyworkofdenver.example where info can be gathered about me and services/fees for brochure.
Updates

Just increased budget. Please see new feedback in discussion thread.

Thanks!

                                       HEY ALL,

Just wanted to let you know that I made a change to my website. It is on the Prices Page. I no longer have the frequent  flyer prices but I added discounts. Let me know if you have any questions. Thanks so much!

Target Market(s)

healthy, urban, educated, upper middle class, yogis

Industry/Entity Type

Marketing

Requirements
Must have
• logo stays purple
Should not have
• not too busy

```html
<!DOCTYPE html>
<html lang="en">
<head>
<meta charset="utf-8">
<title>Lumo Bodywork of Denver – Brochure Cover</title>
<link rel="stylesheet" href="https://fonts.googleapis.com/css2?family=Mulish:wght@300;400;600&display=swap">
<style>
  :root {
    --gold-light: #d9d4bd;
    --gold-mid: #b3ab8a;
    --gold-deep: #8a8264;
    --stone-dark: #5e5a4c;
    --magenta: #d6378f;
    --magenta-soft: #e45ca5;
    --plum: #8e2a85;
    --blush: #f0b6cf;
    --violet: #7b2fa6;
    --white: #ffffff;
  }
  * { margin: 0; padding: 0; box-sizing: border-box; }
  html, body { width: 1200px; height: 800px; overflow: hidden; background: #efeee9; }
  .brochure {
    position: relative;
    width: 1200px;
    height: 800px;
    overflow: hidden;
    font-family: "Mulish", sans-serif;
    background: radial-gradient(ellipse at 78% 40%, var(--gold-light) 0%, var(--gold-mid) 55%, var(--gold-deep) 100%);
  }
  .brochure__art { position: absolute; inset: 0; width: 1200px; height: 800px; }
  .contact {
    position: absolute;
    top: 58px;
    left: 640px;
    width: 340px;
    text-align: center;
    color: var(--violet);
    font-size: 19px;
    line-height: 1.3;
    font-weight: 400;
  }
  .contact__block + .contact__block { margin-top: 16px; }
  .brand {
    position: absolute;
    top: 300px;
    left: 790px;
    width: 320px;
    display: flex;
    flex-direction: column;
    align-items: center;
    gap: 34px;
    color: var(--violet);
  }
  .brand__mark {
    width: 150px;
    height: 150px;
    border: 3px solid var(--violet);
    border-radius: 50%;
  }
  .brand__name {
    font-size: 92px;
    font-weight: 300;
    letter-spacing: 14px;
    line-height: 1;
  }
  .tagline {
    position: absolute;
    left: 700px;
    top: 612px;
    width: 460px;
    color: var(--white);
    text-transform: uppercase;
    font-weight: 400;
    font-size: 31px;
    line-height: 1.1;
    letter-spacing: 1px;
  }
  .tagline__line--lead { display: block; padding-left: 20px; }
  .tagline__line--close { display: block; margin-top: 26px; }
</style>
</head>
<body>
<main class="brochure">
  <svg class="brochure__art" viewBox="0 0 1200 800" aria-hidden="false">
    <defs>
      <linearGradient id="stonePhoto" x1="0" y1="0" x2="1" y2="0">
        <stop offset="0" stop-color="#6f6a58"/>
        <stop offset="0.55" stop-color="#9b9377"/>
        <stop offset="1" stop-color="#b3ab8a" stop-opacity="0"/>
      </linearGradient>
      <linearGradient id="pinkGround" x1="0" y1="0" x2="0" y2="1">
        <stop offset="0" stop-color="#e05fa8"/>
        <stop offset="1" stop-color="#c42f83"/>
      </linearGradient>
    </defs>
    <rect class="photo" role="img" aria-label="Photo of stacked smooth spa stones in front of bamboo stalks" x="0" y="0" width="720" height="800" fill="url(#stonePhoto)"/>
    <path class="band band--pink-ground" d="M0 470 C200 450 380 560 520 650 C640 720 760 770 900 800 L0 800 Z" fill="url(#pinkGround)"/>
    <path class="band band--plum-swoosh" d="M420 0 C540 120 520 300 560 420 C620 600 820 660 1200 660 L1200 780 C820 770 540 720 460 560 C390 430 480 200 360 0 Z" fill="var(--plum)" opacity="0.85"/>
    <path class="stripe stripe--blush" d="M480 0 C610 150 600 410 720 540 C820 640 1000 620 1200 590" fill="none" stroke="var(--blush)" stroke-width="22"/>
    <path class="stripe stripe--white" d="M300 170 C420 230 470 380 520 520 C580 690 900 735 1200 720" fill="none" stroke="var(--white)" stroke-width="8" opacity="0.85"/>
    <path class="band band--magenta-base" d="M0 760 C400 770 800 790 1200 770 L1200 800 L0 800 Z" fill="var(--magenta)"/>
  </svg>

  <address class="contact">
    <div class="contact__block">
      1480 E 7th Ave. Denver, CO 80218<br>
      p. 303.555.0142<br>
      E. info@lumobodyworkofdenver.example
    </div>
    <div class="contact__block">
      Tues - Fri 10am - 8pm Sat<br>
      10am-5pm
    </div>
    <div class="contact__block">
      (Appointments required)<br>
      No walk-ins please.
    </div>
  </address>

  <div class="brand">
    <span class="brand__mark" aria-hidden="true"></span>
    <span class="brand__name">LUMO</span>
  </div>

  <p class="tagline">
    <span class="tagline__line--lead">Your path to<br>wellness</span>
    <span class="tagline__line--close">Begins here!</span>
  </p>
</main>
</body>
</html>
```